Small Business Consulting Firm Needs Letterhead

We need a letterhead for our company "Brightpath Plus". Our company does outbound calling and mailing to business owner's companies who have taken high interest loans. These loans tend to put these businesses in a big financial bind short term, and we help them find better financial options. We would like the design to match our colors of our logo. Headers and footers would look nice, but we are open. We would want it to include our address, website, phone, and email info. Our address - 2000 E. Lamar Blvd. Suite 600Website - www.safeguardtoday.comEmail - info@safeguardtoday.comPhone - 855-726-1938
Industry/Entity Type
Financial Planning
Look and feel
Each slider illustrates characteristics of the customer's brand and the style your logo design should communicate.

```html
<!DOCTYPE html>
<html lang="en">
<head>
<meta charset="utf-8">
<title>Brightpath Plus Letterhead</title>
<link rel="stylesheet" href="https://fonts.googleapis.com/css2?family=Arimo:wght@400;700&family=Montserrat:wght@400&display=swap">
<style>
  :root {
    --brand-blue: #0a78c6;
    --brand-green: #64a338;
    --ink: #1c1c1c;
    --name-grey: #3a3a3a;
    --paper: #ffffff;
  }
  * { margin: 0; padding: 0; box-sizing: border-box; }
  html, body { width: 973px; height: 1200px; overflow: hidden; background: var(--paper); }
  .letterhead {
    position: relative;
    width: 973px;
    height: 1200px;
    background: var(--paper);
    font-family: "Arimo", Arial, sans-serif;
    color: var(--ink);
  }
  .top-rule {
    position: absolute; left: 0; top: 0; width: 100%; height: 6px;
    background: var(--brand-blue);
  }
  .top-rule-accent {
    position: absolute; left: 0; top: 9px; width: 100%; height: 2px;
    background: var(--brand-green);
  }
  .brand {
    position: absolute; left: 80px; top: 150px;
    display: flex; align-items: center; gap: 14px;
  }
  .brand-square {
    width: 26px; height: 26px; background: var(--brand-green);
  }
  .brand-name {
    font-family: "Montserrat", Arial, sans-serif;
    font-weight: 400; font-size: 28px; letter-spacing: 2px;
    color: var(--name-grey);
  }
  .contact {
    position: absolute; right: 80px; top: 110px;
    text-align: right; font-size: 17px; line-height: 34px;
  }
  .contact-label { color: var(--brand-blue); font-weight: 700; }
  .letter-body {
    position: absolute; left: 134px; top: 326px; width: 705px;
    font-size: 19.6px; line-height: 23.6px;
  }
  .salutation { margin-bottom: 45px; }
  .letter-body p.paragraph { text-align: justify; margin-bottom: 21px; }
  .closing { position: absolute; left: 134px; top: 896px; font-size: 19.6px; }
  .signature {
    position: absolute; left: 138px; top: 930px; width: 96px; height: 62px;
    background: linear-gradient(135deg, #f1f1f1, #dcdcdc);
  }
  .footer-band {
    position: absolute; left: 0; top: 1136px; width: 100%; height: 32px;
    background: var(--brand-green);
  }
  .footer-url {
    position: absolute; right: 56px; top: 5px;
    font-size: 19px; letter-spacing: 4px; color: var(--paper);
  }
</style>
</head>
<body>
<div class="letterhead">
  <div class="top-rule"></div>
  <div class="top-rule-accent"></div>

  <div class="brand">
    <div class="brand-square"></div>
    <div class="brand-name">BRIGHTPATH PLUS</div>
  </div>

  <div class="contact">
    <div><span class="contact-label">Phone</span> - 855-726-1938</div>
    <div><span class="contact-label">Email</span> - info@brightpathplus.com</div>
    <div>4170 W. Corwin Ave. Suite 310</div>
  </div>

  <div class="letter-body">
    <p class="salutation">Dear :</p>
    <p class="paragraph">Lorem ipsum dolor sit amet, consectetur adipiscing elit. Aenean ut ipsum eget massa hendrerit vestibulum vel in velit. Donec pretium neque velit.</p>
    <p class="paragraph">Aliquam porta lectus nec mauris ornare venenatis. Vivamus non est turpis, et cursus sem. Mauris vehicula erat in diam auctor at bibendum nisl lacinia.</p>
    <p class="paragraph">Morbi imperdiet neque vehicula nunc convallis gravida. Vestibulum iaculis pretium placerat. Integer consequat, est sit amet facilisis eleifend, nibh nibh varius orci, eget dapibus arcu dui non purus. Pellentesque in magna mauris. Duis enim sapien, dictum vitae condimentum a, pulvinar vel lacus. Mauris et molestie nibh. Vestibulum vitae nulla at metus elementum porta sit amet interdum elit. Nulla sollicitudin neque eu nulla volutpat congue.</p>
    <p class="paragraph">Etiam pellentesque, velit id dapibus fermentum, turpis sapien ornare dui, ac tincidunt ligula odio congue purus. Nunc sed ante dui, in porta lectus. Cras nec sem lorem. In hac habitasse platea dictumst. Maecenas id diam quis dui porta tristique. Sed id egestas felis. Donec ullamcorper mattis posuere. Phasellus fermentum eleifend tortor vel dapibus. Vestibulum ante ipsum.</p>
  </div>

  <p class="closing">Sincerely,</p>
  <div class="signature" role="img" aria-label="Handwritten signature of the sender"></div>

  <div class="footer-band">
    <div class="footer-url">www.brightpathplus.com</div>
  </div>
</div>
</body>
</html>
```